Gardening and life coaching business card design

I need business cards for a new company in the heart of the Ozarks at the Lake of the Ozarks. Maple Hollow Unlimited's mission is to teach the world to fish. We provide fresh local fish and produce using permaculture methods. We work with nature and the flow to create more harmony and less impact. We also coach others who are ready to make this transition. We specialize in microgreens and Aquaculture systems. I would like to make Maple Hollow Unlimited come alive with green vines and purple flowers I wold like Maple Hollow Unlimited to be in green and the rest of the lettering to be in purple. The feel of the card should be that of the Garden of Eden.

Life Coaching

Maple Hollow Unlimited
Owner/Operator Dorothea Fenwick
Contact Info:
(555) 214-0683
maplehollowunlimited.com
maplehollowunlimited is also on FB

```html
<!DOCTYPE html>
<html lang="en">
<head>
<meta charset="utf-8">
<title>Maple Hollow Unlimited – Business Cards</title>
<link href="https://fonts.googleapis.com/css2?family=Open+Sans:wght@700&family=Inter:wght@300;400&display=swap" rel="stylesheet">
<style>
  :root {
    --backdrop: #3a3a3e;
    --card: #f4faf8;
    --brand-green: #2f8f2a;
    --leaf-green: #3fae35;
    --leaf-faint: #dfe8e1;
    --ink-purple: #4b2a6b;
    --ink-purple-soft: #6a4a8a;
    --icon-bg: #0d0d0d;
    --rule: #555555;
  }
  * { box-sizing: border-box; margin: 0; padding: 0; }
  html, body {
    width: 1200px; height: 960px; overflow: hidden;
    background: var(--backdrop);
  }
  .card {
    position: absolute;
    width: 700px; height: 400px;
    background: var(--card);
    box-shadow: 0 6px 18px rgba(0,0,0,.35);
    overflow: hidden;
  }
  .card--front { left: 60px; top: 50px; }
  .card--back { left: 440px; top: 510px; }

  .brand {
    position: absolute;
    font-family: "Open Sans", sans-serif;
    font-weight: 700;
    color: var(--brand-green);
    letter-spacing: -0.5px;
    white-space: nowrap;
  }
  .mark {
    position: absolute;
    border-radius: 50%;
  }
  .card--front .mark {
    left: 420px; top: 110px; width: 170px; height: 170px;
    background: var(--leaf-faint);
  }
  .card--front .brand {
    left: 0; right: 0; top: 172px;
    text-align: center; font-size: 44px;
  }
  .card--back .brand {
    left: 50px; top: 110px; font-size: 26px;
  }
  .card--back .mark {
    left: 360px; top: 100px; width: 44px; height: 44px;
    background: var(--leaf-green);
  }
  .person {
    position: absolute; right: 310px; top: 250px;
    font-family: "Inter", sans-serif; text-align: right;
  }
  .person__name { font-weight: 300; font-size: 27px; color: var(--ink-purple); }
  .person__role { font-weight: 400; font-size: 14px; color: var(--ink-purple-soft); margin-top: 2px; }

  .divider {
    position: absolute; left: 425px; top: 90px;
    width: 1px; height: 220px;
    background: linear-gradient(var(--card), var(--rule) 30%, var(--rule) 70%, var(--card));
  }
  .contacts {
    position: absolute; left: 448px; top: 120px;
    list-style: none;
    font-family: "Inter", sans-serif; font-weight: 300;
    font-size: 16px; color: var(--ink-purple);
  }
  .contacts li { display: flex; align-items: center; gap: 10px; height: 40px; white-space: nowrap; }
  .contacts svg { width: 26px; height: 26px; flex: none; }
</style>
</head>
<body>
  <section class="card card--front" aria-label="Card front">
    <div class="mark" aria-hidden="true"></div>
    <p class="brand">Maple Hollow Unlimited</p>
  </section>

  <section class="card card--back" aria-label="Card back">
    <p class="brand">Maple Hollow Unlimited</p>
    <div class="mark" aria-hidden="true"></div>
    <div class="person">
      <p class="person__name">Dorothea Fenwick</p>
      <p class="person__role">Owner/Operator</p>
    </div>
    <div class="divider"></div>
    <ul class="contacts">
      <li>
        <svg viewBox="0 0 26 26" aria-hidden="true">
          <rect width="26" height="26" rx="4" fill="var(--icon-bg)"/>
          <path d="M8 7 l3 0 1 4 -2 1.5 q1.5 3 4 4.5 l1.5-2 4 1 0 3 q-7 0 -11.5-12z" fill="var(--leaf-green)"/>
        </svg>
        (555) 214-0683
      </li>
      <li>
        <svg viewBox="0 0 26 26" aria-hidden="true">
          <rect width="26" height="26" rx="4" fill="var(--icon-bg)"/>
          <circle cx="13" cy="13" r="7" fill="none" stroke="var(--leaf-green)" stroke-width="1.6"/>
          <ellipse cx="13" cy="13" rx="3" ry="7" fill="none" stroke="var(--leaf-green)" stroke-width="1.2"/>
          <line x1="6" y1="13" x2="20" y2="13" stroke="var(--leaf-green)" stroke-width="1.2"/>
        </svg>
        maplehollowunlimited.com
      </li>
      <li>
        <svg viewBox="0 0 26 26" aria-hidden="true">
          <rect width="26" height="26" rx="4" fill="var(--icon-bg)"/>
          <rect x="9" y="9" width="8" height="8" fill="var(--leaf-green)"/>
        </svg>
        maplehollowunlimited
      </li>
    </ul>
  </section>
</body>
</html>
```